New Wix logo and website layout

I need a new logo design and a new, modern website layout design. I am a professional therapist providing remedial massage. I am Canadian but live in Australia & would like the logo to have a somewhat 'Canadian feel' to it (something subtle i.e. no flags) I currently have a maple tree leaf as my logo. my current website is tidewaterbodywork.com.au. I need the website to work on mobile phones & traditional web browsers.

Target Market(s)

customers looking for remedial massage and manual lymphatic drainage

Industry/Entity Type

professional massage

Coding

Coded - Design and coding required

Font styles to use
Sans Serif

Colors
EB3D1F
EC4F4E
F09395
F8D3D4
FCEDEE

Requirements
Nice to have
• something subtle that indicates that I am canadian
Should not have
• no flags. nothing too bold

```html
<!DOCTYPE html>
<html lang="en">
<head>
<meta charset="utf-8">
<title>Tidewater Bodywork</title>
<link rel="stylesheet" href="https://fonts.googleapis.com/css2?family=Oswald:wght@500&family=Roboto:wght@400;500;700&family=Fira+Sans:wght@400;500&display=swap">
<style>
:root{
  --red:#eb3d1f;
  --red-soft:#ec4f4e;
  --pink:#f09395;
  --blush:#f8d3d4;
  --mist:#fcedee;
  --dark:#2b2b2b;
  --ink:#1f1f1f;
  --grey:#6a6a6a;
  --white:#fff;
}
*{box-sizing:border-box;margin:0;padding:0}
html,body{width:1200px;height:3232px;overflow:hidden}
body{position:relative;background:var(--white);font-family:Roboto,sans-serif;color:var(--ink)}
.abs{position:absolute}
.heading{font-family:Oswald,sans-serif;font-weight:500;text-transform:uppercase;color:var(--ink);letter-spacing:.3px}
.heading span{color:var(--red)}
.btn{position:absolute;background:var(--red);color:var(--white);font-weight:700;text-transform:uppercase;display:flex;align-items:center;justify-content:center;border-radius:2px}

/* top bar */
.topbar{left:0;top:0;width:1200px;height:43px;background:var(--dark);color:var(--white);font-size:13.5px}
.topbar .info{left:112px;top:13px;display:flex;align-items:center;gap:12px}
.topbar .socials{right:112px;top:6px;display:flex;gap:6px}
.topbar .socials i{display:block;width:31px;height:31px;border:1px solid #bbb;border-radius:50%}

/* header */
.header{left:0;top:43px;width:1200px;height:94px;background:var(--white)}
.brand{display:flex;align-items:center;gap:10px}
.brand .dot{width:34px;height:34px;border-radius:50%;background:var(--red)}
.brand b{font-family:Oswald,sans-serif;font-weight:500;font-size:15px;color:var(--ink);text-transform:uppercase;letter-spacing:.3px}
.nav{top:38px;font-size:15px;font-weight:500;color:var(--ink)}
.nav.active{color:var(--red)}

/* hero */
.hero{left:0;top:137px;width:1200px;height:650px}
.hero-photo{position:absolute;inset:0;clip-path:path("M0 0 H1200 V490 Q600 780 0 470 Z");
  background:
    radial-gradient(ellipse 170px 230px at 620px 60px,#ffffff 0%,#f4f1ee 60%,rgba(244,241,238,0) 100%),
    radial-gradient(ellipse 260px 120px at 760px 330px,#c98a62 0%,#b87550 45%,rgba(184,117,80,0) 100%),
    radial-gradient(ellipse 200px 110px at 1020px 420px,#b67250 0%,#8f5638 40%,rgba(143,86,56,0) 100%),
    radial-gradient(ellipse 130px 90px at 930px 240px,#5a3a2a 0%,rgba(90,58,42,0) 100%),
    radial-gradient(ellipse 420px 150px at 350px 470px,#f3efeb 0%,#e4ddd6 50%,rgba(228,221,214,0) 100%),
    linear-gradient(100deg,#f6f3ef 0%,#ede6df 35%,#e8ddd2 60%,#e7e2dc 85%,#f2efeb 100%)}
.hero h1{left:110px;top:168px;font-size:45px}
.hero p{left:112px;top:236px;font-family:'Fira Sans',sans-serif;font-size:17px;line-height:28px;color:#222}
.dots{left:566px;top:576px;display:flex;gap:7px}
.dots i{width:12px;height:12px;border:1.5px solid #555;border-radius:50%;display:block}
.dots i.on{background:var(--red);border-color:var(--red)}

/* leaf backdrops */
.leafwash{position:absolute}

/* about */
.ring{border-radius:50%;background:var(--red)}
.ring-photo{border-radius:50%}
.about h2{left:634px;top:893px;font-size:41px}
.about p{left:634px;width:454px;font-size:14.5px;line-height:25.7px;color:var(--grey);text-align:justify}

/* services */
.services h2{left:0;width:1200px;text-align:center;top:1473px;font-size:41px}
.card{width:300px;height:428px;background:var(--white);border-radius:8px;box-shadow:0 2px 14px rgba(0,0,0,.12);top:1571px;text-align:center}
.card .ph{position:absolute;left:7px;top:7px;width:286px;height:208px}
.card h3{position:absolute;left:0;width:100%;top:238px;font-size:18px;font-weight:500;text-transform:uppercase}
.card .rule{position:absolute;left:125px;top:265px;width:50px;height:2px;background:var(--red)}
.card p{position:absolute;left:20px;width:260px;top:281px;font-size:14px;line-height:24px;color:#888}
.card .btn{left:98px;top:369px;width:103px;height:38px;font-size:10.5px}
.arrow{width:38px;height:38px;border-radius:50%;top:1766px;display:flex;align-items:center;justify-content:center;box-shadow:0 1px 6px rgba(0,0,0,.15)}

/* contact */
.contact h2{left:110px;top:2287px;font-size:41px}
.field{background:var(--white);border:1px solid #eee;font-size:14.5px;color:#555;padding:0 17px;display:flex;align-items:center}
.field.msg{align-items:flex-start;padding-top:16px}

/* footer */
.footer-title{font-size:17px;font-weight:500;color:var(--white);text-transform:uppercase}
.flink{left:365px;font-size:15px;color:var(--white);display:flex;align-items:center;gap:20px}
.flink i{width:13px;height:13px;border-radius:50%;background:var(--red);display:block}
.cinfo b{display:block;font-size:14.5px;font-weight:500;color:var(--white);margin-bottom:4px}
.cinfo span{font-size:12px;line-height:20px;color:var(--white)}
.round{width:44px;height:44px;border-radius:50%}
</style>
</head>
<body>

<div class="abs topbar">
  <div class="abs info">
    <svg width="12" height="15" viewBox="0 0 12 15"><path d="M6 0a6 6 0 0 0-6 6c0 4 6 9 6 9s6-5 6-9a6 6 0 0 0-6-6zm0 8.3a2.3 2.3 0 1 1 0-4.6 2.3 2.3 0 0 1 0 4.6z" fill="#fff"/></svg>
    <span>Jenna Hart 14 Ferncliff Road Cheltenham VIC 3192</span>
    <span style="margin:0 10px">|</span>
    <svg width="13" height="13" viewBox="0 0 24 24"><path d="M6.6 10.8a15 15 0 0 0 6.6 6.6l2.2-2.2a1 1 0 0 1 1-.25 11.4 11.4 0 0 0 3.6.57 1 1 0 0 1 1 1V20a1 1 0 0 1-1 1A17 17 0 0 1 3 4a1 1 0 0 1 1-1h3.5a1 1 0 0 1 1 1c0 1.25.2 2.45.57 3.57a1 1 0 0 1-.25 1z" fill="#fff"/></svg>
    <span>0412 555 019</span>
  </div>
  <div class="abs socials"><i></i><i></i><i></i></div>
</div>

<div class="abs header">
  <div class="abs brand" style="left:110px;top:30px"><span class="dot"></span><b>Tidewater Bodywork</b></div>
  <div class="abs nav active" style="left:383px">Home</div>
  <div class="abs nav" style="left:456px">Remedial Massage</div>
  <div class="abs nav" style="left:617px">About Me</div>
  <div class="abs nav" style="left:715px">Fees</div>
  <div class="abs nav" style="left:779px">Contact</div>
  <div class="btn" style="left:900px;top:27px;width:188px;height:43px;font-size:12px">Book an Appointment</div>
</div>

<!-- faint autumn-leaf backdrops -->
<div class="leafwash" role="img" aria-label="Faint scattered autumn maple leaves behind the about section" style="left:0;top:790px;width:1200px;height:620px;background:
  radial-gradient(ellipse 230px 200px at 1080px 130px,rgba(246,205,180,.45),rgba(255,255,255,0)),
  radial-gradient(ellipse 180px 150px at 60px 230px,rgba(246,210,190,.4),rgba(255,255,255,0)),
  radial-gradient(ellipse 260px 120px at 280px 560px,rgba(248,214,190,.45),rgba(255,255,255,0)),
  radial-gradient(ellipse 220px 140px at 960px 520px,rgba(247,218,198,.4),rgba(255,255,255,0)),
  radial-gradient(ellipse 200px 130px at 1150px 350px,rgba(250,225,205,.35),rgba(255,255,255,0))"></div>
<div class="leafwash" role="img" aria-label="Soft blurred autumn maple leaves behind the contact section" style="left:0;top:2060px;width:1200px;height:720px;background:
  radial-gradient(ellipse 380px 280px at 180px 420px,rgba(238,180,160,.35),rgba(255,255,255,0)),
  radial-gradient(ellipse 300px 200px at 120px 120px,rgba(244,196,176,.35),rgba(255,255,255,0)),
  radial-gradient(ellipse 320px 220px at 560px 560px,rgba(242,200,184,.3),rgba(255,255,255,0)),
  radial-gradient(ellipse 260px 200px at 1100px 620px,rgba(246,210,196,.3),rgba(255,255,255,0)),
  linear-gradient(180deg,#fff 0%,#fdf3ef 40%,#fbefea 100%)"></div>

<section class="abs hero">
  <div class="hero-photo" role="img" aria-label="Therapist giving a back massage to a client lying on a treatment table in a bright room"></div>
  <svg class="abs" style="left:0;top:0" width="1200" height="650" viewBox="0 0 1200 650"><path d="M0 470 Q600 780 1200 490 L1200 505 Q600 810 0 482 Z" fill="#eb3d1f"/></svg>
  <h1 class="abs heading">Tidewater <span>Bodywork</span></h1>
  <p class="abs">I completed my training in Toronto, Canada in 1999 where<br>I obtained a Diploma of Remedial Massage</p>
  <div class="btn" style="left:112px;top:313px;width:140px;height:50px;font-size:14px">Get Started</div>
  <div class="abs dots"><i></i><i class="on"></i><i></i><i></i></div>
</section>

<section class="about">
  <div class="abs ring" style="left:112px;top:860px;width:444px;height:444px"></div>
  <div class="abs ring-photo" role="img" aria-label="Portrait of the therapist seated at a desk in a light office" style="left:131px;top:860px;width:408px;height:408px;background:
    radial-gradient(ellipse 120px 160px at 210px 140px,#e8c7a0 0%,#d8b080 50%,rgba(216,176,128,0) 100%),
    radial-gradient(ellipse 220px 130px at 200px 380px,#8ea2d4 0%,#7f95cb 50%,rgba(127,149,203,0) 100%),
    linear-gradient(160deg,#f4f2ef 0%,#ebe6df 45%,#e2ddd6 100%)"></div>
  <h2 class="abs heading">About <span>Me</span></h2>
  <p class="abs" style="top:963px">I completed my training in Toronto, Canada in 1999 where I obtained a Diploma of Remedial Massage through the Northern Institute of Massage Therapy.</p>
  <p class="abs" style="top:1053px">Over the years, I have practiced in several different settings including medical centre, chiropractic clinic, spa and currently am a sole trader in my own practice. I have been helping my clients achieve better health through my treatments for several years. I take special interest in women's health.</p>
  <div class="btn" style="left:634px;top:1211px;width:129px;height:50px;font-size:14px">Read More</div>
</section>

<section class="services">
  <svg class="abs" style="left:0;top:1380px" width="1200" height="820" viewBox="0 0 1200 820">
    <path d="M0 164 Q460 -140 1200 176 L1200 652 Q620 1000 0 632 Z" fill="#fcedee"/>
    <path d="M0 164 Q460 -140 1200 176" fill="none" stroke="#eb3d1f" stroke-width="5"/>
    <path d="M0 632 Q620 1000 1200 652" fill="none" stroke="#eb3d1f" stroke-width="5"/>
  </svg>
  <h2 class="abs heading">Our <span>Services</span></h2>

  <div class="abs card" style="left:128px">
    <div class="ph" role="img" aria-label="Client receiving a head and face massage beside tropical leaves" style="background:
      radial-gradient(ellipse 90px 70px at 230px 110px,#3c3330 0%,rgba(60,51,48,0) 100%),
      radial-gradient(ellipse 80px 50px at 70px 170px,#3f6b4a 0%,rgba(63,107,74,0) 100%),
      radial-gradient(ellipse 120px 80px at 150px 60px,#e2c7b2 0%,rgba(226,199,178,0) 100%),
      linear-gradient(135deg,#f3f0ec,#e6dcd2 60%,#cbd0c4)"></div>
    <h3>Remedial Massage</h3><div class="rule"></div>
    <p>Remedial massage is used to help relieve tension and stress in the soft tissues of the body including muscles</p>
    <div class="btn">Read More</div>
  </div>
  <div class="abs card" style="left:449px">
    <div class="ph" role="img" aria-label="Deep tissue back massage at an outdoor spa with candles and flowers" style="background:
      radial-gradient(ellipse 100px 60px at 150px 40px,#f4f1ec 0%,rgba(244,241,236,0) 100%),
      radial-gradient(ellipse 150px 45px at 150px 120px,#d6a07a 0%,rgba(214,160,122,0) 100%),
      radial-gradient(ellipse 150px 40px at 150px 185px,#8a4e2c 0%,rgba(138,78,44,0) 100%),
      linear-gradient(135deg,#1f3a1c,#3c6a34 40%,#223a20)"></div>
    <h3>Deep Tissue</h3><div class="rule"></div>
    <p>At vero eos et accusamus et iusto odio dignissimos ducimus qui blanditiis praesentium voluptatum</p>
    <div class="btn">Read More</div>
  </div>
  <div class="abs card" style="left:771px">
    <div class="ph" role="img" aria-label="Couple lying side by side receiving therapeutic back massages" style="background:
      radial-gradient(ellipse 90px 60px at 60px 60px,#5a3a2c 0%,rgba(90,58,44,0) 100%),
      radial-gradient(ellipse 100px 60px at 130px 150px,#4a3128 0%,rgba(74,49,40,0) 100%),
      radial-gradient(ellipse 160px 110px at 180px 110px,#d39a74 0%,rgba(211,154,116,0) 100%),
      linear-gradient(135deg,#eee8e2,#dcb898 55%,#c08566)"></div>
    <h3>Therapeutic</h3><div class="rule"></div>
    <p>At vero eos et accusamus et iusto odio dignissimos ducimus qui blanditiis praesentium voluptatum</p>
    <div class="btn">Read More</div>
  </div>

  <div class="abs arrow" style="left:49px;background:#fff"><svg width="12" height="16" viewBox="0 0 12 16"><path d="M9 2 3 8l6 6" fill="none" stroke="#222" stroke-width="2.5"/></svg></div>
  <div class="abs arrow" style="left:1113px;background:var(--red)"><svg width="12" height="16" viewBox="0 0 12 16"><path d="m3 2 6 6-6 6" fill="none" stroke="#fff" stroke-width="2.5"/></svg></div>
</section>

<section class="contact">
  <h2 class="abs heading">Get in <span>Touch</span></h2>
  <div class="abs field" style="left:112px;top:2380px;width:239px;height:49px">First Name</div>
  <div class="abs field" style="left:362px;top:2380px;width:239px;height:49px">Last Name</div>
  <div class="abs field" style="left:112px;top:2442px;width:239px;height:49px">Your Phone</div>
  <div class="abs field" style="left:362px;top:2442px;width:239px;height:49px">Your Email</div>
  <div class="abs field msg" style="left:112px;top:2506px;width:489px;height:111px">Message</div>
  <div class="btn" style="left:112px;top:2633px;width:171px;height:50px;font-size:15px">Send Message</div>

  <div class="abs ring" style="left:644px;top:2269px;width:444px;height:444px"></div>
  <div class="abs ring-photo" role="img" aria-label="Client with towel-wrapped hair receiving a shoulder massage in a spa room" style="left:659px;top:2265px;width:414px;height:414px;background:
    radial-gradient(ellipse 90px 130px at 60px 230px,#c9cde8 0%,rgba(201,205,232,0) 100%),
    radial-gradient(ellipse 110px 70px at 230px 170px,#e0b7a3 0%,rgba(224,183,163,0) 100%),
    radial-gradient(ellipse 160px 120px at 260px 320px,#f1f1f3 0%,rgba(241,241,243,0) 100%),
    radial-gradient(ellipse 140px 80px at 300px 60px,#bcc3d6 0%,rgba(188,195,214,0) 100%),
    linear-gradient(150deg,#dfe3ee 0%,#eceef3 45%,#e6dad6 100%)"></div>
</section>

<footer>
  <svg class="abs" style="left:0;top:2770px" width="1200" height="462" viewBox="0 0 1200 462"><path d="M0 160 Q520 -170 1200 173 V462 H0 Z" fill="#2b2b2b"/><path d="M0 160 Q520 -170 1200 173" fill="none" stroke="#eb3d1f" stroke-width="5"/></svg>

  <div class="abs" style="left:110px;top:3010px;width:200px;text-align:center">
    <div style="width:60px;height:60px;border-radius:50%;background:var(--red);margin:0 auto 22px"></div>
    <div class="heading" style="color:#fff;font-size:21px">Tidewater Bodywork</div>
  </div>

  <div class="abs footer-title" style="left:365px;top:2928px">Quick Links</div>
  <div class="abs flink" style="top:2969px"><i></i>Home</div>
  <div class="abs flink" style="top:3009px"><i></i>About Us</div>
  <div class="abs flink" style="top:3048px"><i></i>Our Services</div>
  <div class="abs flink" style="top:3088px"><i></i>Resources</div>
  <div class="abs flink" style="top:3127px"><i></i>Contact</div>

  <div class="abs footer-title" style="left:541px;top:2928px">Contact Info</div>
  <svg class="abs" style="left:541px;top:2970px" width="11" height="14" viewBox="0 0 12 15"><path d="M6 0a6 6 0 0 0-6 6c0 4 6 9 6 9s6-5 6-9a6 6 0 0 0-6-6zm0 8.3a2.3 2.3 0 1 1 0-4.6 2.3 2.3 0 0 1 0 4.6z" fill="#eb3d1f"/></svg>
  <div class="abs cinfo" style="left:575px;top:2968px"><b>Address:</b><span>Jenna Hart 14 Ferncliff Road<br>Cheltenham VIC 3192</span></div>
  <svg class="abs" style="left:541px;top:3041px" width="13" height="13" viewBox="0 0 24 24"><path d="M6.6 10.8a15 15 0 0 0 6.6 6.6l2.2-2.2a1 1 0 0 1 1-.25 11.4 11.4 0 0 0 3.6.57 1 1 0 0 1 1 1V20a1 1 0 0 1-1 1A17 17 0 0 1 3 4a1 1 0 0 1 1-1h3.5a1 1 0 0 1 1 1c0 1.25.2 2.45.57 3.57a1 1 0 0 1-.25 1z" fill="#eb3d1f"/></svg>
  <div class="abs cinfo" style="left:575px;top:3038px"><b>Phone:</b><span>0412 555 019</span></div>
  <svg class="abs" style="left:541px;top:3112px" width="15" height="11" viewBox="0 0 15 11"><rect width="15" height="11" rx="1" fill="#eb3d1f"/><path d="m1 1 6.5 5L14 1" fill="none" stroke="#2b2b2b" stroke-width="1.4"/></svg>
  <div class="abs cinfo" style="left:575px;top:3108px"><b>Email:</b><span>jenna@tidewaterbodywork.com.au</span></div>

  <div class="abs footer-title" style="left:804px;top:2928px">Newsletter Signup</div>
  <div class="abs field" style="left:804px;top:2973px;width:284px;height:49px;border:2px solid #fff">Email Address</div>
  <div class="btn" style="left:981px;top:2977px;width:103px;height:41px;font-size:14px">Sign Up</div>
  <div class="abs round" style="left:805px;top:3046px;background:var(--red)"></div>
  <div class="abs round" style="left:856px;top:3046px;background:#fff"></div>
  <div class="abs round" style="left:907px;top:3046px;background:#fff"></div>

  <div class="abs" style="left:110px;top:3173px;width:978px;height:1px;background:#555"></div>
  <div class="abs" style="left:0;width:1200px;top:3191px;text-align:center;font-size:13.5px;color:#fff">© 2022 <b style="font-weight:500">TIDEWATER BODYWORK</b> &nbsp;|&nbsp; All Rights Reserved</div>
</footer>

</body>
</html>
```